Redesign website for small print company

Vindurgata is a small printing company in Iceland mainly servicing Students, schools, etc. We are also doing all kind of other jobs, like business cards, book printing, brochure printing etc. We are also selling books online.
Our website is: www.vindurgata.is
What we are looking for is:
- Web Design (Uncoded - PSD layout only)
- Mobile friendly design, using our current color scheme: Red, green, yellow and light gray.
- Clean simple design
- Simple, light and easy to use.
- More menu Items/drop down
Industry/Entity Type
Digital Printing
Number of Pages Required
5+ page
Requirements
Must have
- Easy navigation
- Designed for mobile
- Current color scheme (see logo)
Nice to have
- Icon based products

```html
<!DOCTYPE html>
<html lang="is">
<head>
<meta charset="utf-8">
<title>Vindurgata – prentþjónusta</title>
<link rel="stylesheet" href="https://fonts.googleapis.com/css2?family=Lato:ital,wght@0,300;0,400;0,700;1,400&family=Montserrat:wght@400;600;700&display=swap">
<style>
:root{
  --green:#0e6b34;
  --red:#e8403f;
  --yellow:#fcdc1f;
  --hero-yellow:#f2cf10;
  --black:#0b0b0b;
  --ink:#222;
  --grey:#a9a9a9;
  --light:#f1f2f4;
  --line:#e4e4e4;
  --white:#fff;
}
*{box-sizing:border-box;margin:0;padding:0}
html,body{width:1200px;height:3125px;overflow:hidden}
body{font-family:"Lato",sans-serif;color:var(--ink);background:var(--white);position:relative}
.abs{position:absolute}

.topbar{top:0;left:0;width:1200px;height:42px;background:var(--green);color:var(--white);font-size:15px;font-weight:700}
.topbar span{position:absolute;top:12px;display:flex;align-items:center;gap:8px}
.topbar svg{width:16px;height:16px}

.header{top:42px;left:0;width:1200px;height:73px;background:var(--white)}
.brand{position:absolute;left:77px;top:16px;display:flex;align-items:center;gap:12px;font-family:"Lato",sans-serif;font-weight:700;font-size:36px;color:var(--black);letter-spacing:.5px}
.brand i{display:block;width:40px;height:40px;background:var(--red)}
.nav a{position:absolute;top:26px;font-size:16px;color:#c4c4c4;text-decoration:none}
.nav a.active{color:var(--green)}
.nav .divider{position:absolute;left:1073px;top:18px;width:3px;height:34px;background:var(--hero-yellow)}

.hero{top:115px;left:0;width:1200px;height:604px;background:var(--red);overflow:hidden}
.hero-top{position:absolute;left:0;top:0;width:1200px;height:218px;background:var(--hero-yellow)}
.hero-band{position:absolute;left:0;top:218px;width:1200px;height:12px;background:var(--white);opacity:.85}
.hero h1{position:absolute;left:73px;top:75px;font-family:"Lato",sans-serif;font-weight:400;font-size:48px;line-height:52px;color:var(--black)}
.hero h1 span{display:block;padding-left:100px}
.action{position:absolute;top:270px;width:150px;text-align:center;color:var(--white);font-size:21px}
.action .disc{width:104px;height:104px;margin:0 auto 16px;border-radius:50%;background:var(--white);display:flex;align-items:center;justify-content:center}
.action.current .disc{background:var(--red);box-shadow:0 0 0 5px #c73231}
.action.current{font-style:italic}
.action .glyph{width:48px;height:48px;background:var(--red);border-radius:6px}
.action.current .glyph{background:var(--white);border-radius:50%}
.action .q{font-size:64px;font-weight:700;color:var(--red);line-height:1}
.hero-stand{position:absolute;left:729px;top:239px;width:181px;height:271px;background:var(--white)}
.hero-circle{position:absolute;left:735px;top:78px;width:365px;height:365px;border-radius:50%;background:var(--white);padding:10px}
.hero-circle div{width:100%;height:100%;border-radius:50%;background:linear-gradient(180deg,#2c2c2c 0%,#3c7e55 55%,#cfd6d8 100%)}
.dots{position:absolute;top:554px;height:4px}
.dots i{position:absolute;top:0;width:84px;height:4px;background:var(--white);opacity:.9}

.services{top:719px;left:0;width:1200px;height:198px;background:var(--white)}
.services-intro{position:absolute;left:0;top:0;width:300px;height:198px;background:var(--black);color:var(--white);padding:40px 0 0 46px;border-bottom:6px solid var(--hero-yellow)}
.services-intro h2{font-weight:400;font-size:42px;margin-bottom:14px}
.services-intro p{font-size:11.5px;line-height:15px;color:#ddd;width:220px}
.service{position:absolute;top:0;width:150px;height:198px;border-right:1px solid var(--line);text-align:center;font-size:19px;border-bottom:6px solid}
.service .pic{width:70px;height:56px;margin:40px auto 0;border-radius:4px}
.service .label{position:absolute;left:0;top:121px;width:150px;line-height:21px;display:flex;align-items:center;justify-content:center;height:42px}
.service.current{background:var(--light)}

.welcome{top:917px;left:0;width:1200px;height:760px}
.photo-a{position:absolute;left:77px;top:93px;width:523px;height:417px;background:linear-gradient(135deg,#b9d7ef 0%,#f3e3cf 55%,#dfe6ec 100%);clip-path:polygon(0 0,100% 0,100% 48%,71% 48%,71% 100%,0 100%)}
.photo-b{position:absolute;left:77px;top:520px;width:371px;height:167px;background:linear-gradient(90deg,#f0d6e0 0%,#e56f8c 60%,#f4e7ee 100%)}
.welcome-text{position:absolute;left:502px;top:310px;width:600px}
.eyebrow{color:var(--red);font-size:14px}
.welcome-text h2{font-weight:400;font-size:46px;margin:8px 0 12px;color:var(--black)}
.welcome-text p{font-size:13.5px;line-height:20px;color:#c8c8c8;margin-bottom:14px}

.products{top:1677px;left:0;width:1200px;height:660px;background:var(--yellow);text-align:center}
.products .eyebrow{position:absolute;left:0;top:70px;width:1200px;font-size:14px}
.products h2{position:absolute;left:0;top:94px;width:1200px;font-weight:400;font-size:42px;color:var(--black)}
.card-frame{position:absolute;left:433px;top:150px;width:334px;height:448px;border:2px solid #e3c21a;background:#f7d61c}
.product{position:absolute;top:198px;width:320px}
.product .pic{width:220px;height:156px;margin:0 auto;background:linear-gradient(135deg,#3b4a8c 0%,#b8c3d6 45%,#8d3140 100%);border-radius:4px}
.product h3{font-weight:400;font-size:25px;margin-top:48px;color:var(--black)}
.product .price{font-family:"Montserrat",sans-serif;font-weight:700;font-size:29px;color:#5a5a5a;margin-top:6px}
.btn{display:inline-block;margin-top:20px;width:156px;height:52px;line-height:52px;border-radius:26px;background:var(--black);color:var(--white);font-family:"Montserrat",sans-serif;font-size:16px}
.btn.outline{background:transparent;border:2px solid var(--black);color:var(--black);line-height:48px}
.arrow{position:absolute;top:2008px;width:24px;height:24px}

.newsletter{top:2337px;left:0;width:1200px;height:340px;text-align:center}
.newsletter .eyebrow{position:absolute;left:0;top:78px;width:1200px}
.newsletter h2{position:absolute;left:0;top:100px;width:1200px;font-weight:400;font-size:44px;color:var(--black)}
.newsletter p{position:absolute;left:300px;top:164px;width:600px;font-size:16px;line-height:26px;color:#444}
.subscribe{position:absolute;left:340px;top:227px;width:516px;height:50px;border:1px solid #bbb;border-radius:25px;text-align:left}
.subscribe span{position:absolute;left:28px;top:16px;font-style:italic;font-size:14px;color:#555}
.subscribe b{position:absolute;right:3px;top:3px;width:62px;height:42px;border-radius:21px;background:var(--red);color:var(--white);font-family:"Montserrat",sans-serif;font-size:20px;line-height:42px;text-align:center;font-weight:600}

.map{top:2677px;left:0;width:1200px;height:313px;background:linear-gradient(90deg,#0b0d10 0%,#1e2530 40%,#3f5566 70%,#6d8698 100%)}
.pin{position:absolute;left:860px;top:140px}

.footer{top:2990px;left:0;width:1200px;height:135px;background:var(--white)}
.footer h4{position:absolute;top:30px;font-weight:400;font-size:14px;color:var(--red)}
.fb{position:absolute;left:77px;top:60px;width:46px;height:46px;border:2px solid #555;border-radius:50%}
.pay{position:absolute;top:72px;width:48px;height:30px;border:2px solid #222;border-radius:4px;background:var(--white)}
.pay.dark{background:var(--black)}
.footer .brand{left:466px;top:46px;font-size:28px}
.footer .brand i{width:30px;height:30px}
.footer-links{position:absolute;left:782px;top:42px;font-size:14px;color:#333;word-spacing:2px}
.footer-links span{color:#999;margin:0 14px}
.copy{position:absolute;left:782px;top:70px;font-size:14px;color:#333}
.copy em{font-style:normal;color:var(--red)}
</style>
</head>
<body>

<div class="abs topbar">
  <span style="left:675px">
    <svg viewBox="0 0 24 24" fill="#e8403f"><path d="M6.6 10.8a15 15 0 0 0 6.6 6.6l2.2-2.2c.3-.3.7-.4 1-.2 1.1.4 2.3.6 3.6.6.6 0 1 .4 1 1V20c0 .6-.4 1-1 1A17 17 0 0 1 3 4c0-.6.4-1 1-1h3.5c.6 0 1 .4 1 1 0 1.3.2 2.5.6 3.6.1.3 0 .7-.2 1z"/></svg>555 0142</span>
  <span style="left:825px">
    <svg viewBox="0 0 24 24" fill="#e8403f"><path d="M2 5h20v14H2z"/><path d="M2 5l10 8 10-8" fill="none" stroke="#0e6b34" stroke-width="2"/></svg>verk@vindurgata.is</span>
  <span style="left:1015px">
    <svg viewBox="0 0 24 24" fill="none" stroke="#e8403f" stroke-width="3"><circle cx="10" cy="10" r="6"/><path d="M15 15l6 6"/></svg>Search</span>
</div>

<header class="abs header">
  <div class="brand"><i></i>VINDURGATA</div>
  <nav class="nav">
    <a class="active" style="left:562px">Home</a>
    <a style="left:648px">About Us</a>
    <a style="left:754px">Services</a>
    <a style="left:854px">Job Submit</a>
    <a style="left:975px">Contact Us</a>
    <i class="divider"></i>
    <svg class="abs" style="left:1090px;top:16px" width="34" height="40" viewBox="0 0 34 40" fill="none" stroke="#555" stroke-width="2"><path d="M4 12h26l-2 26H6z"/><path d="M11 12V8a6 6 0 0 1 12 0v4"/><text x="17" y="32" font-size="13" fill="#555" stroke="none" text-anchor="middle" font-family="Lato,sans-serif">0</text></svg>
  </nav>
</header>

<section class="abs hero">
  <div class="hero-top"></div>
  <div class="hero-band"></div>
  <h1>Engar áhyggjur<span>...þetta reddast</span></h1>
  <div class="action" style="left:65px"><div class="disc"><div class="glyph" role="img" aria-label="Sending document icon"></div></div>SENDA VERK</div>
  <div class="action current" style="left:242px"><div class="disc"><div class="glyph" role="img" aria-label="Design palette icon"></div></div>HANNA VERK</div>
  <div class="action" style="left:419px"><div class="disc"><span class="q">?</span></div>FA TILBOD</div>
  <div class="hero-stand"></div>
  <div class="hero-circle"><div role="img" aria-label="Printed calendars and photo books around a desktop screen"></div></div>
  <div class="dots"><i style="left:462px"></i><i style="left:558px"></i><i style="left:652px"></i></div>
</section>

<section class="abs services">
  <div class="services-intro">
    <h2>Services</h2>
    <p>Vindurgata er fyrirtæki staðsett á háskólasvæðinu sem hefur sérhæft sig í að þjónusta skólafólk.</p>
  </div>
  <div class="service current" style="left:300px;border-bottom-color:var(--hero-yellow)"><div class="pic" role="img" aria-label="Stack of essay papers" style="background:linear-gradient(180deg,#e8403f,#fcdc1f,#0e6b34)"></div><div class="label">ESSAYS</div></div>
  <div class="service" style="left:450px;border-bottom-color:var(--red)"><div class="pic" role="img" aria-label="Business cards" style="background:linear-gradient(135deg,#e8403f,#b52c2c)"></div><div class="label">BUSINESS<br>CARD</div></div>
  <div class="service" style="left:600px;border-bottom-color:var(--green)"><div class="pic" role="img" aria-label="Folded leaflet" style="background:linear-gradient(90deg,#0e6b34,#1a1a1a,#e8403f)"></div><div class="label">LEAFLEATS</div></div>
  <div class="service" style="left:750px;border-bottom-color:var(--hero-yellow)"><div class="pic" role="img" aria-label="Stack of printed books" style="background:linear-gradient(180deg,#3d6fb0,#e8403f,#f2a31b)"></div><div class="label">BOOK<br>PRINTING</div></div>
  <div class="service" style="left:900px;border-bottom-color:var(--black)"><div class="pic" role="img" aria-label="Posters" style="background:linear-gradient(135deg,#f2a31b,#e8403f,#6b2b6b)"></div><div class="label">POSTERS</div></div>
  <div class="service" style="left:1050px;border-bottom-color:var(--red)"><div class="pic" role="img" aria-label="Stack of textbooks" style="background:linear-gradient(180deg,#e8403f,#3aa88a,#f2a31b)"></div><div class="label">TEXTBOOKS</div></div>
</section>

<section class="abs welcome">
  <div class="photo-a" role="img" aria-label="Designer choosing colours from swatches and a tablet"></div>
  <div class="photo-b" role="img" aria-label="Printing press with ink cartridges"></div>
  <div class="welcome-text">
    <div class="eyebrow">Welcome To</div>
    <h2>Vindurgata</h2>
    <p>Vindurgata er fyrirtæki staðsett á háskólasvæðinu sem hefur sérhæft sig í að þjónusta skólafólk, ásamt því að sinna allri almennri prentun fyrir almenning.</p>
    <p>Vindurgata gefur út greinasöfn og frumsamdar kennslubækur fyrir námskeið, prentar lokaritgerðir fyrir nema, auk þess að vinna við ótalinn fjölda smærri verka fyrir nemendur, kennara og stofnanir. Má þar nefna bæklinga, skýrslur, spurningalista, nafnspjöld, bækur, OCR skönnun og fleira.</p>
    <p>Vindurgata er umhverfisvottuð prentsmiðja. Við notum vottaðan pappír og umhverfisvænt blek, sem hefur skapað okkur gott orðspor hér á landi og meðal viðskiptavina.</p>
    <p>Vindurgata er staðsett á horninu á Hlíðargötu og Brekkugötu. (gengið inn Brekkugötumegin).</p>
  </div>
</section>

<section class="abs products">
  <div class="eyebrow">We Offer</div>
  <h2>Products</h2>
  <div class="card-frame"></div>
  <div class="product" style="left:98px"><div class="pic" role="img" aria-label="A3 folded leaflets fanned out"></div><h3>A3 Folded Leaflat</h3><div class="price">1.000 Kr</div><span class="btn">SHOP NOW</span></div>
  <div class="product" style="left:440px"><div class="pic" role="img" aria-label="A4 folded leaflets fanned out"></div><h3>A4 foldad Leaflat</h3><div class="price">1.000 Kr</div><span class="btn outline">SHOP NOW</span></div>
  <div class="product" style="left:796px"><div class="pic" role="img" aria-label="Finance brochures fanned out"></div><h3>Batter Finances</h3><div class="price">3.900 Kr</div><span class="btn">SHOP NOW</span></div>
</section>
<svg class="arrow" style="left:26px" viewBox="0 0 24 24"><path d="M2 12l10-9v6h10v6H12v6z" fill="#111"/></svg>
<svg class="arrow" style="left:1150px" viewBox="0 0 24 24"><path d="M22 12L12 3v6H2v6h10v6z" fill="#111"/></svg>

<section class="abs newsletter">
  <div class="eyebrow">Subscribe</div>
  <h2>Newsletter</h2>
  <p>Subscribe to our Mailing List. Join Our amazing Community &amp; Get Latest Updates About Us.</p>
  <div class="subscribe"><span>Enter Your E-Mail</span><b>GO!</b></div>
</section>

<section class="abs map" role="img" aria-label="Street map showing the shop location near the university">
  <svg class="pin" width="26" height="36" viewBox="0 0 26 36"><path d="M13 0a13 13 0 0 1 13 13c0 10-13 23-13 23S0 23 0 13A13 13 0 0 1 13 0z" fill="#e8403f"/><circle cx="13" cy="13" r="5" fill="#8e1f1f"/></svg>
</section>

<footer class="abs footer">
  <h4 style="left:77px">Follow us</h4>
  <div class="fb"></div>
  <h4 style="left:256px">We Accept</h4>
  <div class="pay" style="left:252px"></div>
  <div class="pay dark" style="left:310px"></div>
  <div class="brand"><i></i>VINDURGATA</div>
  <div class="footer-links">Home<span>/</span>Services<span>/</span>kil á verkum<span>/</span>To okkur</div>
  <div class="copy">© <em>Vindurgata</em> - 2018. All Rights Reserved.</div>
</footer>

</body>
</html>
```